VELMOR Website Design

We need a website designed for our company VELMOR. We are a luxury lifestyle club that will provide benefits and services for our members. The site should be clean & sleek, preferably using black and white (or darker colors). (example sites: stravenhall.example, plinth.example)

Here is a link of a sample page I did using wix. (https://dunmere7.sitehostly.example/mysite) This can be used to get a general idea.

Target Market(s)

Upper Middle Class in the United States

Number of Pages Required

5+ page

Font styles to use
Sans Serif
Other font styles liked:
• Arial (or other similar fonts)

Requirements
Must have
• A clean design that is eye-catching and speaks to our company.
Nice to have
• Ideas for copy.

```html
<!DOCTYPE html>
<html lang="en">
<head>
<meta charset="utf-8">
<title>VELMOR — Members Only Lifestyle Club</title>
<link href="https://fonts.googleapis.com/css2?family=Montserrat:wght@400;600;700;800&family=Open+Sans:wght@400;600&display=swap" rel="stylesheet">
<style>
:root{
  --black:#000;
  --white:#fff;
  --paper:#f3f0f0;
  --ink:#111;
  --muted:#444;
  --rule:#cfcfcf;
  --card-shadow:0 6px 18px rgba(0,0,0,.14);
}
*{margin:0;padding:0;box-sizing:border-box}
html,body{width:1200px;height:3863px;overflow:hidden;background:var(--white)}
body{position:relative;font-family:"Open Sans",Arial,sans-serif;color:var(--ink)}
.abs{position:absolute}
.head{font-family:"Montserrat",Arial,sans-serif}

/* hero */
.hero{left:0;top:0;width:1200px;height:657px;
  background:radial-gradient(ellipse at 30% 40%,#b88a62 0%,#6b3e2a 40%,#2b1712 100%)}
.hero-glow{left:0;top:0;width:1200px;height:657px;
  background:radial-gradient(circle at 75% 35%,rgba(190,60,40,.45),transparent 45%),linear-gradient(180deg,rgba(0,0,0,.35),transparent 30%)}
.brand{left:41px;top:26px;font-family:"Montserrat",Arial,sans-serif;font-weight:800;font-size:34px;color:var(--white);letter-spacing:1px}
.nav{right:40px;top:22px;display:flex;gap:10px;align-items:center}
.nav a{font-family:"Montserrat",Arial,sans-serif;font-weight:700;font-size:14px;color:var(--white);text-decoration:none;padding:7px 12px;letter-spacing:.3px}
.nav a.active{background:var(--white);color:var(--black)}
.nav a.apply{border:2px solid var(--white);padding:5px 12px}
.dots{left:540px;top:594px;display:flex;gap:14px}
.dots span{width:10px;height:10px;border-radius:50%;background:var(--white)}
.dots span.on{background:transparent;border:2px solid var(--white);width:14px;height:14px;margin-top:-2px}

/* welcome */
.welcome{left:0;top:657px;width:1200px;height:347px;background:var(--paper)}
.welcome-copy{left:124px;top:708px;width:230px}
.dash{width:48px;height:3px;background:var(--black)}
.welcome-copy .eyebrow{font-family:"Montserrat",Arial,sans-serif;font-weight:600;font-size:14px;margin-top:18px}
.welcome-copy h1{font-family:"Montserrat",Arial,sans-serif;font-weight:800;font-size:40px;line-height:1.05;margin-top:4px}
.welcome-copy p{font-size:13.5px;line-height:1.5;color:var(--muted);margin-top:26px}
.welcome-copy p + p{margin-top:16px}
.stats{left:450px;top:705px;width:280px;height:260px}
.stat{position:absolute;width:140px}
.stat .ico{width:30px;height:30px;border-radius:50%;background:var(--black);display:flex;align-items:center;justify-content:center}
.stat .num{font-family:"Montserrat",Arial,sans-serif;font-weight:600;font-size:30px;margin-top:12px}
.stat .lbl{font-family:"Montserrat",Arial,sans-serif;font-weight:600;font-size:12.5px;margin-top:6px}
.stats .vline{position:absolute;left:110px;top:0;width:1px;height:260px;background:var(--rule)}
.stats .hline{position:absolute;left:0;top:128px;width:280px;height:1px;background:var(--rule)}
.join-card{left:772px;top:592px;width:297px;height:412px;background:var(--white);box-shadow:var(--card-shadow);text-align:center}
.join-card .dash{margin:105px auto 0;width:40px;height:2px}
.join-card h2{font-family:"Montserrat",Arial,sans-serif;font-weight:400;font-size:25px;line-height:1.3;margin-top:30px}
.btn{display:inline-block;font-family:"Montserrat",Arial,sans-serif;font-weight:700;font-size:14px;letter-spacing:.3px;text-decoration:none}
.btn-dark{background:var(--black);color:var(--white);padding:14px 30px}
.btn-light{background:var(--white);color:var(--black);padding:14px 24px}
.join-card .btn{margin-top:34px}

/* services */
.services-title{left:0;top:1072px;width:1200px;text-align:center}
.services-title .dash{margin:0 auto;width:44px}
.services-title h2{font-family:"Montserrat",Arial,sans-serif;font-weight:800;font-size:27px;margin-top:14px;letter-spacing:.5px}
.service{width:224px;height:208px;background:var(--white);box-shadow:var(--card-shadow);text-align:center}
.service svg{margin-top:40px}
.service .dash{width:34px;height:1px;background:#999;margin:26px auto 0}
.service h3{font-family:"Montserrat",Arial,sans-serif;font-weight:600;font-size:14px;margin-top:22px}
.service.featured{background:var(--black);color:var(--white)}
.service.featured .dash{background:#777}

/* dark feature band */
.dark-band{left:0;top:1924px;width:1200px;height:1076px;background:var(--black)}
.photo-exp{left:131px;top:2016px;width:528px;height:404px;
  background:radial-gradient(circle at 70% 20%,#c9743a 0%,#5b2d22 40%,#140b0b 100%)}
.photo-ben{left:541px;top:2518px;width:528px;height:402px;
  background:radial-gradient(circle at 35% 25%,#d4a050 0%,#6c4a2a 45%,#1c160e 100%)}
.feature{color:var(--white);width:330px}
.feature .dash{background:var(--white);width:96px;height:3px}
.feature h2{font-family:"Montserrat",Arial,sans-serif;font-weight:700;font-size:25px;margin-top:14px;letter-spacing:.5px}
.feature p{font-size:13.5px;line-height:1.55;margin-top:22px}
.feature .btn{margin-top:30px}

/* applications */
.apps{left:0;top:3000px;width:1200px;height:489px;
  background:radial-gradient(circle at 30% 40%,#7a2f4e 0%,#3a1630 40%,#0c0710 100%)}
.apps-sparkle{left:0;top:3000px;width:1200px;height:489px;
  background:radial-gradient(circle at 80% 30%,rgba(90,120,200,.35),transparent 40%)}
.apps-tab{left:662px;top:3000px;width:407px;height:80px;background:var(--black);color:var(--white);padding:0 0 0 56px}
.apps-tab .dash{background:var(--white);width:48px;height:2px;margin-top:0}
.apps-tab h2{font-family:"Montserrat",Arial,sans-serif;font-weight:600;font-size:25px;margin-top:20px}
.apps-copy{left:713px;top:3240px;width:470px;color:var(--white);font-size:18.5px;line-height:1.38;font-weight:600}
.apps-btn{left:713px;top:3399px}

/* footer */
.footer-brand{left:134px;top:3588px;font-family:"Montserrat",Arial,sans-serif;font-weight:800;font-size:48px;letter-spacing:1px}
.fcol{top:3548px}
.fcol h4{font-family:"Montserrat",Arial,sans-serif;font-weight:700;font-size:12px;margin-bottom:20px}
.fcol p,.fcol li{font-size:11.5px;line-height:1.45;color:#222;list-style:none}
.contact-row{display:flex;gap:14px;margin-bottom:20px}
.contact-row svg{flex:none;margin-top:2px}
.social-row{display:flex;align-items:center;gap:12px;margin-bottom:16px;font-size:11.5px}
.social-row .dot{width:24px;height:24px;border-radius:50%;background:#1e2a44}
.footer-rule{left:134px;top:3764px;width:935px;height:1px;background:#ddd}
.copyright{left:0;top:3810px;width:1200px;text-align:center;font-size:11px;color:#222}
</style>
</head>
<body>

<!-- Hero -->
<div class="abs hero" role="img" aria-label="Photo of friends smiling and raising glasses in a toast at an evening party"></div>
<div class="abs hero-glow"></div>
<div class="abs brand">VELMOR</div>
<nav class="abs nav">
  <a class="active" href="#">HOME</a>
  <a href="#">ABOUT</a>
  <a href="#">SERVICES AND BENEFITS</a>
  <a href="#">CONTACT US</a>
  <a class="apply" href="#">APPLY</a>
</nav>
<div class="abs dots"><span></span><span></span><span class="on"></span><span></span><span></span></div>

<!-- Welcome -->
<section class="abs welcome"></section>
<div class="abs welcome-copy">
  <div class="dash"></div>
  <div class="eyebrow">WELCOME TO</div>
  <h1>VELMOR</h1>
  <p>VELMOR is a members only lifestyle club founded in order to bring the best services, experiences, and opportunities to our diverse community of members.</p>
  <p>Our members consist of creatives, athletes, artists, and other professionals.</p>
</div>
<div class="abs stats">
  <div class="vline"></div><div class="hline"></div>
  <div class="stat" style="left:0;top:0">
    <div class="ico"><svg width="14" height="14" viewBox="0 0 14 14"><rect x="1" y="2" width="12" height="11" fill="none" stroke="#fff" stroke-width="1.6"/><line x1="1" y1="5.5" x2="13" y2="5.5" stroke="#fff" stroke-width="1.6"/></svg></div>
    <div class="num">6</div><div class="lbl">EVENTS</div>
  </div>
  <div class="stat" style="left:148px;top:0">
    <div class="ico"><svg width="14" height="14" viewBox="0 0 14 14"><circle cx="7" cy="4.5" r="3" fill="#fff"/><path d="M1.5 13c0-3.2 2.5-5 5.5-5s5.5 1.8 5.5 5z" fill="#fff"/></svg></div>
    <div class="num">35</div><div class="lbl">MEMBERS</div>
  </div>
  <div class="stat" style="left:0;top:155px">
    <div class="ico"><svg width="14" height="14" viewBox="0 0 14 14"><rect x="1" y="4" width="12" height="8" fill="#fff"/><rect x="4.5" y="1.5" width="5" height="3" fill="none" stroke="#fff" stroke-width="1.4"/></svg></div>
    <div class="num">35</div><div class="lbl">PROJECTS</div>
  </div>
  <div class="stat" style="left:148px;top:155px">
    <div class="ico"><svg width="14" height="14" viewBox="0 0 14 14"><rect x="1.5" y="2.5" width="10" height="10" fill="none" stroke="#fff" stroke-width="1.5"/><path d="M6 9l6-7" stroke="#fff" stroke-width="1.6"/></svg></div>
    <div class="num">12</div><div class="lbl">YEARS EXPERIENCE</div>
  </div>
</div>
<div class="abs join-card">
  <div class="dash"></div>
  <h2>A Members<br>Only Lifestyle Club</h2>
  <a class="btn btn-dark" href="#">APPLY</a>
</div>

<!-- Services -->
<div class="abs services-title"><div class="dash"></div><h2>SERVICES</h2></div>

<div class="abs service" style="left:234px;top:1164px">
  <svg width="52" height="52" viewBox="0 0 52 52" fill="none" stroke="#222" stroke-width="2.5"><rect x="4" y="9" width="44" height="38" rx="3"/><line x1="4" y1="19" x2="48" y2="19"/><line x1="15" y1="4" x2="15" y2="13"/><line x1="37" y1="4" x2="37" y2="13"/><g fill="#222" stroke="none"><rect x="11" y="25" width="6" height="5"/><rect x="23" y="25" width="6" height="5"/><rect x="35" y="25" width="6" height="5"/><rect x="11" y="35" width="6" height="5"/><rect x="23" y="35" width="6" height="5"/><rect x="35" y="35" width="6" height="5"/></g></svg>
  <div class="dash"></div><h3>Accounting</h3>
</div>
<div class="abs service" style="left:487px;top:1164px">
  <svg width="60" height="52" viewBox="0 0 60 52"><circle cx="38" cy="14" r="11" fill="none" stroke="#222" stroke-width="2.5"/><text x="38" y="19" text-anchor="middle" font-family="Montserrat,sans-serif" font-size="14" font-weight="700" fill="#222">$</text><path d="M4 34h12l10 4h12c3 0 3 5 0 5H26M16 46h26l14-10c2-2-1-5-4-3l-10 6" fill="none" stroke="#222" stroke-width="2.5"/><rect x="2" y="31" width="8" height="18" fill="#222"/></svg>
  <div class="dash"></div><h3>Investment</h3>
</div>
<div class="abs service" style="left:744px;top:1164px">
  <svg width="52" height="52" viewBox="0 0 52 52"><circle cx="26" cy="14" r="10" fill="#222"/><path d="M6 50c0-12 9-20 20-20s20 8 20 20z" fill="#222"/><path d="M23 31l3 12 3-12z" fill="#fff"/></svg>
  <div class="dash"></div><h3>Lawyer</h3>
</div>

<div class="abs service" style="left:234px;top:1401px">
  <svg width="52" height="56" viewBox="0 0 52 56" fill="none" stroke="#222" stroke-width="2.5"><rect x="12" y="4" width="28" height="48"/><line x1="4" y1="52" x2="48" y2="52"/><g fill="#222" stroke="none"><rect x="17" y="10" width="6" height="6"/><rect x="29" y="10" width="6" height="6"/><rect x="17" y="21" width="6" height="6"/><rect x="29" y="21" width="6" height="6"/><rect x="17" y="32" width="6" height="6"/><rect x="29" y="32" width="6" height="6"/><rect x="22" y="42" width="8" height="10"/></g></svg>
  <div class="dash"></div><h3>Real Estate</h3>
</div>
<div class="abs service featured" style="left:487px;top:1401px">
  <svg width="56" height="56" viewBox="0 0 56 56"><circle cx="28" cy="28" r="22" fill="none" stroke="#fff" stroke-width="3"/><circle cx="34" cy="26" r="12" fill="#fff"/><text x="34" y="31" text-anchor="middle" font-family="Montserrat,sans-serif" font-size="13" font-weight="800" fill="#000">24</text><path d="M10 36c4 6 10 10 16 10" fill="none" stroke="#fff" stroke-width="4"/></svg>
  <div class="dash"></div><h3>24/7 Concierge</h3>
</div>
<div class="abs service" style="left:744px;top:1401px">
  <svg width="64" height="52" viewBox="0 0 64 52"><path d="M4 22h20L14 6h7l16 16h16c5 0 8 2 8 4s-3 4-8 4H37L21 46h-7l10-16H4l-2-4z" fill="#222"/></svg>
  <div class="dash"></div><h3>Private Jet Travel</h3>
</div>

<div class="abs service" style="left:234px;top:1640px">
  <svg width="60" height="52" viewBox="0 0 60 52" fill="none" stroke="#222" stroke-width="2.5"><rect x="4" y="8" width="52" height="40" rx="3"/><line x1="4" y1="18" x2="56" y2="18"/><g stroke-width="2"><line x1="12" y1="3" x2="12" y2="12"/><line x1="22" y1="3" x2="22" y2="12"/><line x1="32" y1="3" x2="32" y2="12"/><line x1="42" y1="3" x2="42" y2="12"/><path d="M11 27l3 3 5-5M27 27l3 3 5-5M43 27l3 3 5-5M11 38l3 3 5-5M27 38l3 3 5-5"/></g></svg>
  <div class="dash"></div><h3>Event Access</h3>
</div>
<div class="abs service" style="left:487px;top:1640px">
  <svg width="60" height="56" viewBox="0 0 60 56"><rect x="4" y="8" width="40" height="38" rx="3" fill="#222"/><rect x="4" y="8" width="40" height="8" fill="#222"/><rect x="28" y="30" width="24" height="20" rx="2" fill="#222" stroke="#fff" stroke-width="2"/><path d="M33 30v-6a7 7 0 0114 0v6" fill="none" stroke="#222" stroke-width="3"/><circle cx="40" cy="40" r="2.5" fill="#fff"/></svg>
  <div class="dash"></div><h3>Private Events</h3>
</div>
<div class="abs service" style="left:744px;top:1640px">
  <svg width="56" height="52" viewBox="0 0 56 52"><rect x="4" y="14" width="48" height="34" rx="3" fill="#222"/><rect x="19" y="6" width="18" height="10" rx="2" fill="none" stroke="#222" stroke-width="3"/><line x1="4" y1="28" x2="52" y2="28" stroke="#fff" stroke-width="1.5"/></svg>
  <div class="dash"></div><h3>Experiences</h3>
</div>

<!-- Dark band: experiences & benefits -->
<section class="abs dark-band"></section>
<div class="abs photo-exp" role="img" aria-label="Photo of women laughing and clinking glasses under party lights"></div>
<div class="abs feature" style="left:718px;top:2052px">
  <div class="dash"></div>
  <h2>EXPERIENCES</h2>
  <p>VELMOR organizes and supports a ton of private events and parties for our members.</p>
  <p>Members are also provided access to exclusive venues and events from our partners.</p>
  <p>Network with other members to build lasting relationships.</p>
  <a class="btn btn-light" href="#">READ MORE</a>
</div>
<div class="abs feature" style="left:134px;top:2554px">
  <div class="dash"></div>
  <h2>BENEFITS</h2>
  <p>VELMOR organizes and supports a ton of private events and parties for our members.</p>
  <p>Members are also provided access to exclusive venues and events from our partners.</p>
  <p>Network with other members to build lasting relationships.</p>
  <a class="btn btn-light" href="#">READ MORE</a>
</div>
<div class="abs photo-ben" role="img" aria-label="Photo of a glass raised at a warmly lit dinner gathering"></div>

<!-- Applications -->
<section class="abs apps" role="img" aria-label="Photo of a crowd celebrating with confetti at a night party"></section>
<div class="abs apps-sparkle"></div>
<div class="abs apps-tab"><div class="dash"></div><h2>Applications</h2></div>
<p class="abs apps-copy">Hey - Thanks for your interest! We will begin accepting applications in 2019. In the meantime, simply fill out the indication of interest below and we will be in touch once we begin accepting applications!</p>
<a class="abs btn btn-light apps-btn" href="#">APPLY NOW</a>

<!-- Footer -->
<div class="abs footer-brand">VELMOR</div>
<div class="abs fcol" style="left:445px;width:200px">
  <h4>CONTACT US</h4>
  <div class="contact-row"><svg width="10" height="13" viewBox="0 0 10 13"><path d="M5 0a5 5 0 015 5c0 3.5-5 8-5 8S0 8.5 0 5a5 5 0 015-5z" fill="#222"/><circle cx="5" cy="5" r="1.8" fill="#fff"/></svg><p>118 Larkspur Row<br>Fenwick, IL 60990</p></div>
  <div class="contact-row"><svg width="11" height="11" viewBox="0 0 11 11"><path d="M2 0l2 3-1.2 1.3a7 7 0 003.9 3.9L8 7l3 2-1 2C5 11 0 6 0 1z" fill="#222"/></svg><p>555.014.2290</p></div>
  <div class="contact-row"><svg width="12" height="9" viewBox="0 0 12 9"><rect width="12" height="9" fill="#222"/><path d="M0 0l6 5 6-5" fill="none" stroke="#fff" stroke-width="1.2"/></svg><p>hello@velmorclub.example</p></div>
</div>
<div class="abs fcol" style="left:703px;width:180px">
  <h4>MENU</h4>
  <ul><li>Home</li><li>About</li><li>Services and Benefits</li><li>Contact Us</li><li>Apply</li></ul>
</div>
<div class="abs fcol" style="left:937px;width:150px">
  <h4>CONNECT WITH US</h4>
  <div class="social-row"><span class="dot"></span>Friendlink</div>
  <div class="social-row"><span class="dot"></span>Chirper</div>
  <div class="social-row"><span class="dot"></span>Workwire</div>
</div>
<div class="abs footer-rule"></div>
<p class="abs copyright">Copyrights @ 2018 All Rights Reserved</p>

</body>
</html>
```